Bork Ventures, Inc. Website redesign

Revamp the website, it is old and outdated. www.borkventuresinc.example

Target Market(s)

Information Technology Consulting and Staffing

Coding

Coded - Design and coding required

Number of Pages Required

5+ page

Colors

Designer to choose colors to be used in the design.

Requirements
Must have
• Outlined text boxes just like from the Tolvane.example site. A clean look

```html
<!DOCTYPE html>
<html lang="en">
<head>
<meta charset="utf-8">
<title>Bork Ventures, Inc.</title>
<link href="https://fonts.googleapis.com/css2?family=Lato:wght@300;400;700&family=Cabin:wght@400;500;600&display=swap" rel="stylesheet">
<style>
:root{
  --brand:#8c1023;
  --ink:#1d1d1f;
  --text:#333;
  --light-bg:#efeeec;
  --about-bg:#e6e6e6;
  --nav-bg:rgba(28,30,38,.88);
  --white:#fff;
  --hero-bottom:#151a26;
}
*{margin:0;padding:0;box-sizing:border-box}
html,body{width:1200px;height:3026px;overflow:hidden}
body{font-family:"Lato",sans-serif;color:var(--text);background:var(--white);position:relative}
.abs{position:absolute}
.center{text-align:center}
.heading{font-family:"Cabin",sans-serif;font-weight:500;color:var(--ink)}
.logo{display:flex;align-items:center;gap:14px}
.logo-name{font-family:"Lato",sans-serif;font-weight:700;font-size:38px;letter-spacing:3px;color:var(--ink)}
.logo-mark{width:30px;height:30px;background:var(--brand)}
/* hero */
.hero{left:0;top:0;width:1200px;height:675px;background:linear-gradient(180deg,#5b6c98 0%,#3a4666 22%,#1e2535 55%,var(--hero-bottom) 100%)}
.header-bar{left:0;top:0;width:1200px;height:132px;display:flex;align-items:center;justify-content:center}
.header-bar .logo-name{color:#111}
.nav{left:0;top:132px;width:1200px;height:57px;background:var(--nav-bg);display:flex;justify-content:center;align-items:center;gap:36px}
.nav a{color:var(--white);text-decoration:none;font-size:17px;height:57px;line-height:57px;padding:0 8px}
.nav a.active{border-bottom:3px solid var(--brand)}
.hero-title{left:0;top:370px;width:1200px;font-family:"Cabin",sans-serif;font-weight:500;font-size:70px;color:var(--white)}
.hero-arrow{top:350px}
.scroll-btn{left:571px;top:646px;width:58px;height:58px;border-radius:50%;background:var(--white)}
/* intro */
.intro-title{left:0;top:716px;width:1200px;font-size:42px;line-height:50px}
.intro-text{left:225px;top:850px;width:750px;font-size:12px;line-height:22px;color:var(--text)}
.intro-text p+p{margin-top:22px}
.btn{display:flex;align-items:center;justify-content:center;background:var(--brand);color:var(--white);font-family:"Cabin",sans-serif;font-weight:500;font-size:19px;text-decoration:none}
/* services */
.services{left:0;top:1121px;width:1200px;height:734px;background:var(--light-bg)}
.services-title{left:0;top:1172px;width:1200px;font-size:42px}
.services-text{left:270px;top:1250px;width:660px;font-size:12px;line-height:22px}
.card{top:1338px;width:305px;height:383px;background:var(--white);border:1px solid #dcdcdc;box-shadow:0 1px 4px rgba(0,0,0,.08);text-align:center;padding:28px 30px 0}
.card-icon{display:block;margin:0 auto 20px}
.card h3{font-family:"Cabin",sans-serif;font-weight:500;font-size:28px;line-height:33px;color:var(--ink);margin-bottom:18px}
.card p{font-size:12px;line-height:22px;color:var(--text)}
/* about */
.about{left:0;top:1855px;width:1200px;height:370px;background:var(--about-bg)}
.about-art-bg{left:0;top:1855px;width:378px;height:370px;background:var(--white)}
.about-art{left:112px;top:1867px;width:346px;height:352px;border-radius:50%;background:radial-gradient(circle at 55% 55%,#3456b8 0%,#8fb0e6 38%,#e8eef8 70%,rgba(255,255,255,0) 72%)}
.about-box{left:527px;top:1923px;width:567px;height:212px;background:var(--white);border:1px solid #d8d8d8;box-shadow:0 1px 4px rgba(0,0,0,.08);padding:34px 40px 34px 48px}
.about-box h2{font-size:35px;font-weight:500;margin-bottom:18px}
.about-box p{font-size:14px;line-height:22px;color:var(--text)}
/* support */
.support{left:0;top:2225px;width:1200px;height:346px;background:linear-gradient(90deg,#4b4b4e 0%,#58585c 55%,#6b605a 75%,#3f3c3c 100%)}
.support-photo{left:790px;top:2225px;width:320px;height:346px;background:radial-gradient(ellipse at 50% 45%,#8a6b5c 0%,#5f4c44 45%,rgba(80,70,66,0) 75%)}
.support-title{left:0;top:2290px;width:1200px;font-size:54px;color:var(--white)}
.support-text{left:270px;top:2372px;width:660px;font-size:18px;line-height:21px;color:var(--white)}
.pill{left:486px;top:2455px;width:229px;height:39px;border-radius:20px;background:#222;color:var(--white);font-family:"Lato",sans-serif;font-weight:700;font-size:14px}
/* contact */
.contact{left:0;top:2571px;width:1200px;height:170px;background:var(--light-bg)}
.contact-item{top:2632px;display:flex;gap:16px}
.contact-item h4{font-family:"Cabin",sans-serif;font-weight:500;font-size:21px;color:var(--ink);margin-bottom:10px}
.contact-item p{font-size:13px;line-height:25px;color:var(--text)}
/* footer */
.footer-logo{left:0;top:2805px;width:1200px;display:flex;justify-content:center;align-items:center}
.footer-logo .logo-name{font-size:32px}
.footer-nav{left:0;top:2882px;width:1200px;display:flex;justify-content:center;gap:36px}
.footer-nav a{color:var(--ink);text-decoration:none;font-size:17px}
.social{left:0;top:2933px;width:1200px;display:flex;justify-content:center;gap:26px}
.social span{width:18px;height:18px;border-radius:50%;background:#1d1d1f;display:block}
.copyright{left:0;top:2978px;width:1200px;font-size:13px;color:var(--ink)}
</style>
</head>
<body>

<div class="abs hero" role="img" aria-label="Night city skyline with network lines and glowing nodes"></div>
<header class="abs header-bar">
  <div class="logo"><span class="logo-name">BORK VENTURES</span><span class="logo-mark"></span></div>
</header>
<nav class="abs nav">
  <a class="active" href="#">Home</a><a href="#">About us</a><a href="#">Services</a><a href="#">Strategy</a><a href="#">IT News</a><a href="#">Contact us</a>
</nav>
<svg class="abs hero-arrow" style="left:224px" width="22" height="30" viewBox="0 0 22 30"><path d="M17 4 6 15l11 11" fill="none" stroke="#fff" stroke-width="4"/></svg>
<svg class="abs hero-arrow" style="left:955px" width="22" height="30" viewBox="0 0 22 30"><path d="M5 4l11 11L5 26" fill="none" stroke="#fff" stroke-width="4"/></svg>
<h1 class="abs hero-title center">BORK VENTURES</h1>
<div class="abs scroll-btn"></div>
<svg class="abs" style="left:590px;top:663px" width="20" height="14" viewBox="0 0 20 14"><path d="M4 3l6 6 6-6" fill="none" stroke="#222" stroke-width="3"/></svg>

<h2 class="abs heading intro-title center">Bringing Thought Leadership and<br>Quality to Every Project</h2>
<div class="abs intro-text center">
  <p>Bork Ventures, Inc. is an 8(a) full-service IT consulting company based in the Washington, DC Metro area. We offer specialized, highly customized technology solutions for our customers located throughout the United States. Learn about our Services now.</p>
  <p>No two businesses are the same. We believe the technology supporting your business operations should align with your company. Every project begins with a thorough analysis of your current technology environment. We work with you to define the environment you want. Then we implement industry-proven practices that enable you to achieve your business objectives. We draw on our experience at civilian and federal agencies to generate ideas and create IT solutions that address your unique business needs. Learn about our Strategies.</p>
</div>
<a class="abs btn" href="#" style="left:522px;top:1036px;width:157px;height:48px">Read More</a>

<section class="abs services"></section>
<h2 class="abs heading services-title center">Services</h2>
<p class="abs services-text center">Bork Ventures, Inc. organizes our Services into four key areas. While these four services can be implemented individually the majority of our projects successfully combine components from each. Our people and our process is what makes us successful in providing these services.</p>

<div class="abs card" style="left:106px">
  <svg class="card-icon" width="100" height="80" viewBox="0 0 100 80"><circle cx="28" cy="30" r="22" fill="#e4e4e4"/><rect x="14" y="18" width="40" height="30" rx="3" fill="none" stroke="#333" stroke-width="2.5"/><rect x="50" y="12" width="40" height="28" rx="3" fill="none" stroke="#333" stroke-width="2.5"/><path d="M8 56h52" stroke="#333" stroke-width="2.5"/></svg>
  <h3>Professional<br>Services</h3>
  <p>Multiple IP PBXs on a single instance of SkyExchange is a voipswitch with multi-tenancy architecture supporting many tenants with multiple levels of administration providing different permissions.</p>
</div>
<div class="abs card" style="left:448px">
  <svg class="card-icon" width="100" height="80" viewBox="0 0 100 80"><circle cx="50" cy="40" r="36" fill="none" stroke="#999" stroke-width="2" stroke-dasharray="6 5"/><rect x="24" y="22" width="52" height="36" rx="3" fill="none" stroke="#333" stroke-width="2.5"/><path d="M32 50h36M34 32h10m6 0h12" stroke="#333" stroke-width="2.5"/></svg>
  <h3>Hardware<br>/Software Sales</h3>
  <p>Linkwell is a Desktop &amp; Mobile Unified Communications application designed to provide business users with a set of features and benefits capable of transforming your company communications system into a real powerhouse.</p>
</div>
<div class="abs card" style="left:790px">
  <svg class="card-icon" width="100" height="80" viewBox="0 0 100 80"><circle cx="40" cy="28" r="20" fill="#e4e4e4"/><path d="M26 56a14 14 0 0 1 4-27 20 20 0 0 1 38 4 12 12 0 0 1 0 23Z" fill="none" stroke="#333" stroke-width="2.5"/><path d="M50 36v40M42 42v10m16-10v10" stroke="#333" stroke-width="2.5"/></svg>
  <h3>Technology<br>Assessment</h3>
  <p>Client Hub is a fully-featured telecom customer portal, designed for integration with one or many SkyExchange telephony switches. Client Hub has a friendly GUI that enables efficient, automated billing, invoicing and payments</p>
</div>
<a class="abs btn" href="#" style="left:481px;top:1743px;width:237px;height:48px">View More Services</a>

<section class="abs about"></section>
<div class="abs about-art-bg"></div>
<div class="abs about-art" role="img" aria-label="Illustration of an IT consultant in a cape beside a laptop and a security shield"></div>
<div class="abs about-box">
  <h2 class="heading">About us</h2>
  <p>Bork Ventures, Inc. is an 8(a) innovative and rapidly growing full-service IT consulting firm. We provide our clients with cutting-edge technologies and the know-how to apply them to their individual business models</p>
</div>

<section class="abs support" role="img" aria-label="Photo of a smiling support agent in an office"></section>
<div class="abs support-photo"></div>
<h2 class="abs heading support-title center">Support</h2>
<p class="abs support-text center">Lorem ipsum dolor sit amet, consectetur adipiscing elit, sed do eiusmod tempor incididunt ut labore et dolore magna aliqua. Ut enim ad minim veniam, quis nostrud exercitation ullamco</p>
<a class="abs btn pill" href="#">Remote Support Access</a>

<section class="abs contact"></section>
<div class="abs contact-item" style="left:76px">
  <svg width="32" height="44" viewBox="0 0 32 44"><path d="M16 2C8 2 2 8 2 16c0 10 14 26 14 26s14-16 14-26C30 8 24 2 16 2Z" fill="#222"/><circle cx="16" cy="16" r="5" fill="var(--light-bg)"/></svg>
  <div><h4>Address</h4><p>2280 Larkfield Ct,<br>Hollowmere, MD 20999, USA</p></div>
</div>
<div class="abs contact-item" style="left:475px">
  <svg width="36" height="38" viewBox="0 0 36 38"><path d="M9 2l6 9-4 4c2 5 6 9 11 11l4-4 8 6-4 6C17 34 3 20 3 8Z" fill="#222"/></svg>
  <div><h4>Call Us</h4><p>301-555-0148 (Office)</p></div>
</div>
<div class="abs contact-item" style="left:882px">
  <svg width="36" height="40" viewBox="0 0 36 40"><rect x="0" y="14" width="36" height="24" rx="2" fill="#222"/><path d="M1 16l17 12 17-12" fill="none" stroke="var(--light-bg)" stroke-width="2.5"/></svg>
  <div><h4>Support</h4><p>support@borkventures.example</p></div>
</div>

<div class="abs footer-logo">
  <div class="logo"><span class="logo-name">BORK VENTURES</span><span class="logo-mark" style="width:26px;height:26px"></span></div>
</div>
<nav class="abs footer-nav">
  <a href="#">Home</a><a href="#">About us</a><a href="#">Services</a><a href="#">Strategy</a><a href="#">IT News</a><a href="#">Contact us</a>
</nav>
<div class="abs social"><span></span><span></span><span></span></div>
<p class="abs copyright center">© 2019 &nbsp;|&nbsp; www.borkventuresinc.example</p>

</body>
</html>
```